Velk Partners Building Business Cards

We need a business card that reflects our business as "Solar Experts" in San Diego. Browse our website www.velkpartners.example our License needs to be displayed as "CSLB# 3867140" our phone number is (619) 555-0187

Save thousands on your electric bills and increase the value of your home while helping to protect the environment. Our solar installation experts will help you design the system that's right for you, using only the highest quality equipment that will look great and give you ideal performance. Our goal is to make you energy independent, and get your electric bill to 0.

Paul Osterby
(619) 555-0187
paul@velkpartners.example

Target Market(s)

Home owners in san diego looking for solar

Industry/Entity Type

Solar Energy

Contact Information for Business Card

Paul Osterby
(619) 555-0187
paul@velkpartners.example

Font styles to use
Other font styles liked:
• Use our logo font

Requirements
Must have
• License needs to be displayed as "CSLB# 3867140" our phone number is (619) 555-0187
Nice to have
• Real images of rooftop home solar in san diego
Should not have
• our business address

```html
<!DOCTYPE html>
<html lang="en">
<head>
<meta charset="utf-8">
<title>Velk Partners Building — Business Card</title>
<link href="https://fonts.googleapis.com/css2?family=Montserrat:wght@800&family=Cinzel:wght@400;600&display=swap" rel="stylesheet">
<style>
  :root {
    --stage: #1b1c1e;
    --navy: #164a86;
    --gold: #f2ad1c;
    --white: #ffffff;
    --photo-sky: #5f7f9e;
    --photo-panel: #1d2c5a;
    --photo-roof: #8a8478;
    --photo-green: #3c5a2a;
  }
  * { margin: 0; padding: 0; box-sizing: border-box; }
  html, body { width: 1200px; height: 900px; overflow: hidden; background: var(--stage); }
  .canvas {
    width: 1200px; height: 900px;
    display: flex; flex-direction: column; align-items: center; justify-content: center; gap: 40px;
  }
  .card {
    position: relative; width: 700px; height: 400px; overflow: hidden;
    box-shadow: 0 10px 30px rgba(0,0,0,.5);
  }

  /* Front */
  .card-front .photo {
    position: absolute; inset: 0;
    background:
      linear-gradient(115deg, var(--photo-green) 0%, var(--photo-green) 14%, transparent 14.5%),
      linear-gradient(160deg, var(--photo-sky) 0%, var(--photo-panel) 35%, #26397a 60%, var(--photo-roof) 90%);
  }
  .card-front .shade { position: absolute; inset: 0; background: linear-gradient(180deg, rgba(0,0,0,0) 40%, rgba(0,0,0,.35) 100%); }
  .front-brand {
    position: absolute; left: 150px; top: 150px;
    font-family: 'Montserrat', sans-serif; font-weight: 800;
    color: var(--white); font-size: 46px; line-height: 1.05; letter-spacing: -1px;
  }
  .front-rule { position: absolute; left: 40px; right: 40px; bottom: 60px; height: 2px; background: var(--gold); }
  .front-url {
    position: absolute; right: 70px; bottom: 46px; padding: 0 12px;
    font-family: 'Cinzel', serif; font-size: 15px; color: var(--white);
    background: #3f4760;
  }

  /* Back */
  .card-back { background: var(--navy); color: var(--white); }
  .back-brand {
    position: absolute; left: 50px; top: 110px;
    font-family: 'Montserrat', sans-serif; font-weight: 800;
    font-size: 40px; line-height: 1.05; letter-spacing: -1px;
  }
  .name-tag {
    position: absolute; right: 0; top: 130px; width: 230px; height: 56px;
    background: var(--gold); display: flex; align-items: center; justify-content: center;
    font-family: 'Montserrat', sans-serif; font-weight: 800; font-size: 22px; color: var(--navy);
  }
  .license {
    position: absolute; right: 30px; top: 210px;
    font-family: 'Cinzel', serif; font-size: 16px;
  }
  .license-rule { position: absolute; left: 210px; right: 210px; top: 222px; height: 1.5px; background: var(--gold); }
  .contact-list {
    position: absolute; left: 50px; bottom: 48px; list-style: none;
    font-family: 'Cinzel', serif; font-size: 16px; line-height: 26px;
  }
  .contact-list li { display: flex; align-items: center; gap: 10px; }
  .contact-list svg { width: 14px; height: 14px; fill: var(--gold); }
  .bottom-rule { position: absolute; left: 50px; right: 50px; bottom: 30px; height: 1.5px; background: var(--gold); }
</style>
</head>
<body>
<main class="canvas">
  <section class="card card-front">
    <div class="photo" role="img" aria-label="Photo of rooftop solar panels on a San Diego home"></div>
    <div class="shade"></div>
    <div class="front-brand">Velk Partners<br>Building</div>
    <div class="front-rule"></div>
    <div class="front-url">www.velkpartners.example</div>
  </section>

  <section class="card card-back">
    <div class="back-brand">Velk Partners<br>Building</div>
    <div class="name-tag">Paul Osterby</div>
    <div class="license-rule"></div>
    <div class="license">CSLB# 3867140</div>
    <ul class="contact-list">
      <li>
        <svg viewBox="0 0 24 24" aria-hidden="true"><path d="M6.6 10.8a15.1 15.1 0 0 0 6.6 6.6l2.2-2.2a1 1 0 0 1 1-.25 11.4 11.4 0 0 0 3.6.57 1 1 0 0 1 1 1V20a1 1 0 0 1-1 1A17 17 0 0 1 3 4a1 1 0 0 1 1-1h3.5a1 1 0 0 1 1 1c0 1.25.2 2.45.57 3.57a1 1 0 0 1-.25 1z"/></svg>
        (619) 555-0187
      </li>
      <li>
        <svg viewBox="0 0 24 24" aria-hidden="true"><path d="M2 5h20v14H2zm2 2v.5l8 5 8-5V7zm0 2.9V17h16V9.9l-8 5z"/></svg>
        paul@velkpartners.example
      </li>
      <li>
        <svg viewBox="0 0 24 24" aria-hidden="true"><circle cx="12" cy="12" r="10"/></svg>
        www.velkpartners.example
      </li>
    </ul>
    <div class="bottom-rule"></div>
  </section>
</main>
</body>
</html>
```